"Vine Hollow Excursions" is a top notch Santa Barbara County Wine Tour company.

We provide scenic, boutique and custom wine tours. I need the card to be clean and classy. I will provide our logo. I would like the logo to cover the back side of the card as an option and would like to see a couple color options other then our signature green and gold. I would like to see some creative options and let the designers come up with options.
I need cards for myself and my team. The final design should communicate "An authentic and boutique wine tour experience"
Please use my website for reference www.vinehollowexcursions.example

Target Market(s)

We have a wide range of clients from millennials to baby boomers

Industry/Entity Type

Tour

Contact Information for Business Card

Contact info:
Dale Morton
805-219-6384
info@vinehollowexcursions.example
vinehollowexcursions.example

Colors

Designer to choose colors to be used in the design.

Requirements
Must have
• my logo
Nice to have
• *I would like to have the backside side with the logo and the company statement
• "An authentic and boutique wine tour experience" as an option.
• *I would also like to see what the designers can create!
• *I would like to see an option that incorporates or social: instagram, yelp, trip advisor
Should not have
• I do not want it too busy.

```html
<!DOCTYPE html>
<html lang="en">
<head>
<meta charset="utf-8">
<title>Vine Hollow Excursions – Business Card</title>
<link rel="stylesheet" href="https://fonts.googleapis.com/css2?family=Open+Sans:wght@400;600;700&display=swap">
<style>
  :root {
    --canvas: #ecebe7;
    --card: #ffffff;
    --ink: #222222;
    --ink-soft: #3a3a3a;
    --vine-green: #1f6b3f;
    --gold-light: #d8c3a5;
    --gold: #a88a68;
    --gold-dark: #7d6549;
    --charcoal: #2b2b2b;
  }
  * { box-sizing: border-box; margin: 0; padding: 0; }
  html, body {
    width: 1200px;
    height: 900px;
    overflow: hidden;
    background: var(--canvas);
    font-family: "Open Sans", Arial, sans-serif;
  }
  .canvas {
    width: 1200px;
    height: 900px;
    display: flex;
    flex-direction: column;
    align-items: center;
    justify-content: center;
    gap: 40px;
  }
  .card {
    position: relative;
    width: 700px;
    height: 400px;
    background: var(--card);
    overflow: hidden;
    box-shadow: 0 2px 8px rgba(0,0,0,0.12);
  }

  /* Back side */
  .card-back__scene {
    position: absolute;
    left: 0; top: 0;
    width: 100%;
    height: 260px;
    background: linear-gradient(160deg, #4a4a4a 0%, var(--charcoal) 45%, #111 100%);
  }
  .card-back__rule {
    position: absolute;
    left: 0; top: 260px;
    width: 100%;
    height: 3px;
    background: var(--charcoal);
  }
  .card-back__tagline {
    position: absolute;
    left: 0; right: 0;
    top: 305px;
    text-align: center;
    font-weight: 700;
    font-size: 25px;
    color: var(--ink);
    letter-spacing: 0.2px;
  }

  /* Front side */
  .corner-mark {
    position: absolute;
    left: 0; top: 0;
  }
  .card-front__name {
    position: absolute;
    left: 70px; top: 26px;
    font-weight: 700;
    font-size: 22px;
    color: var(--vine-green);
  }
  .contact-list {
    position: absolute;
    left: 40px; top: 200px;
    list-style: none;
  }
  .contact-list li {
    display: flex;
    align-items: center;
    gap: 9px;
    font-size: 16px;
    color: var(--ink-soft);
    line-height: 26px;
  }
  .contact-list svg { flex: none; }
  .brand {
    position: absolute;
    left: 360px; top: 180px;
    width: 300px;
    display: flex;
    align-items: center;
    gap: 12px;
  }
  .brand__dot {
    flex: none;
    width: 18px; height: 18px;
    border-radius: 50%;
    background: var(--vine-green);
  }
  .brand__name {
    font-weight: 600;
    font-size: 26px;
    line-height: 1.15;
    color: var(--vine-green);
  }
  .footer-band {
    position: absolute;
    left: 0; bottom: 0;
  }
</style>
</head>
<body>
<main class="canvas">

  <section class="card card-back" aria-label="Card back">
    <div class="card-back__scene" role="img" aria-label="Engraved illustration of a sun rising over mountains and vineyard rows"></div>
    <div class="card-back__rule"></div>
    <p class="card-back__tagline">An authentic and boutique wine tour experience</p>
  </section>

  <section class="card card-front" aria-label="Card front">
    <svg class="corner-mark" width="60" height="60" viewBox="0 0 60 60" aria-hidden="true">
      <defs>
        <linearGradient id="goldFill" x1="0" y1="0" x2="1" y2="1">
          <stop offset="0" stop-color="var(--gold-light)"/>
          <stop offset="1" stop-color="var(--gold-dark)"/>
        </linearGradient>
      </defs>
      <polygon points="0,0 40,0 0,40" fill="var(--vine-green)"/>
      <polygon points="44,0 56,0 14,52 0,52 0,46" fill="url(#goldFill)"/>
    </svg>

    <h1 class="card-front__name">Dale Morton</h1>

    <ul class="contact-list">
      <li>
        <svg width="13" height="13" viewBox="0 0 24 24" aria-hidden="true"><path fill="var(--vine-green)" d="M6.6 10.8a15.1 15.1 0 0 0 6.6 6.6l2.2-2.2a1 1 0 0 1 1-.25 11.4 11.4 0 0 0 3.6.57 1 1 0 0 1 1 1V20a1 1 0 0 1-1 1A17 17 0 0 1 3 4a1 1 0 0 1 1-1h3.5a1 1 0 0 1 1 1c0 1.25.2 2.45.57 3.57a1 1 0 0 1-.25 1z"/></svg>
        805-219-6384
      </li>
      <li>
        <svg width="13" height="13" viewBox="0 0 24 24" aria-hidden="true"><rect x="2" y="5" width="20" height="14" rx="1" fill="var(--vine-green)"/><path d="M3 6l9 7 9-7" stroke="#fff" stroke-width="1.8" fill="none"/></svg>
        info@vinehollowexcursions.example
      </li>
      <li>
        <svg width="13" height="13" viewBox="0 0 24 24" aria-hidden="true"><circle cx="12" cy="12" r="10" fill="var(--vine-green)"/><path d="M2 12h20M12 2c3 3 3 17 0 20M12 2c-3 3-3 17 0 20" stroke="#fff" stroke-width="1.5" fill="none"/></svg>
        vinehollowexcursions.example
      </li>
    </ul>

    <div class="brand">
      <span class="brand__dot" aria-hidden="true"></span>
      <span class="brand__name">Vine Hollow Excursions</span>
    </div>

    <svg class="footer-band" width="700" height="48" viewBox="0 0 700 48" aria-hidden="true">
      <defs>
        <linearGradient id="goldBand" x1="0" y1="0" x2="0" y2="1">
          <stop offset="0" stop-color="var(--gold-light)"/>
          <stop offset="1" stop-color="var(--gold-dark)"/>
        </linearGradient>
      </defs>
      <polygon points="0,0 300,0 270,48 0,48" fill="var(--vine-green)"/>
      <polygon points="310,0 700,0 700,48 280,48" fill="url(#goldBand)"/>
    </svg>
  </section>

</main>
</body>
</html>
```